verdant terraces simple classy business card design

my name is colin barrow and I run a gardening business aimed at high class verdant terraces. the business name is verdant terraces and our logo was designed on pixel harbour .My clientel are anything from residential homes to businesses. I take pride in my work and know that I offer a service like no other in my area.
The business card will be used to represent my business and I want it to be not only rememberable, but simplistic and modern. Eye catching too. Of course I would like it relatable to gardening and appealing to the correct clientel - those being garden enthusiasts, prestigious homes and businesses that are after top of the line gardening services like no other on the market.
I am not a typical lawn mowing business so I don't want a typical card design that represents that. The gardens I work with are generally million dollar properties with owners who are very garden proud looking for upkeep and guidance from me along with sometimes whole new garden designs. I want the business cards to show to my clients that I take pride, as they do, in their garden. And I want them to know from my card that I am a professional, qualified horticulturist offering them a top of the line service for life. I want them to refer my business on. I want them to look at my business card and see class and professionalism in a modern unique bold way.
The card should be simple with the possibility of the logo on the front being embossed/debossed and my details on the back the card should have a organic garden feel it's very important to me that it is absolutely perfect
I am also very open to ideas and suggestions so look forward to seeing the designs. the business logo has been supplied with this project and I want the card to be double sided

Contact info is
Colin Barrow - Managing Director / Horticulturist
Phone : 0481 526 704
Email: colinbarrow@verdantterraces.example.au

Target Market(s)

high class gardens residential and commercial

Industry/Entity Type

Gardener

Contact Information for Business Card

Contact info is
Phone : 0481 526 704

PLEASE MAKE CARD DOUBLE SIDED

Requirements
Must have
• organic simple classy modern feel
• must flow with the current logo that has been supplied with this project
• Double sided
• Must explain in a simple way that I deal with high end gardens and I'm a qualified horticulturist
Nice to have
• embossed debossed logo
Should not have
• shouldn't be to busy or cheap looking

```html
<!DOCTYPE html>
<html lang="en">
<head>
<meta charset="utf-8">
<title>Verdant Terraces — Business Card</title>
<link href="https://fonts.googleapis.com/css2?family=Cinzel:wght@400&family=Montserrat:wght@400;700&display=swap" rel="stylesheet">
<style>
  :root {
    --canvas: #e9e8e4;
    --card-dark: #3b3637;
    --card-light: #ffffff;
    --leaf-green: #4f9a55;
    --ink: #4a4a4a;
    --ink-soft: #6b6b6b;
    --rule: #5a5a5a;
  }
  * { box-sizing: border-box; margin: 0; padding: 0; }
  html, body {
    width: 1200px; height: 800px; overflow: hidden;
    background: var(--canvas);
  }
  .stage {
    position: relative; width: 1200px; height: 800px;
    display: flex; align-items: center; justify-content: center; gap: 60px;
  }
  .card {
    position: relative; width: 520px; height: 310px;
    border-radius: 22px;
    box-shadow: 0 10px 30px rgba(0,0,0,.15);
    overflow: hidden;
  }
  /* Front */
  .card-front {
    background: var(--card-dark);
    display: flex; flex-direction: column; align-items: center; justify-content: center;
  }
  .wordmark {
    font-family: "Cinzel", serif; font-weight: 400;
    color: var(--leaf-green); text-align: center; line-height: 1;
  }
  .wordmark-main { display: block; font-size: 46px; letter-spacing: 2px; }
  .wordmark-sub { display: block; font-size: 26px; letter-spacing: 22px; margin-top: 10px; padding-left: 22px; }
  /* Back */
  .card-back {
    background: var(--card-light);
    font-family: "Montserrat", sans-serif;
    color: var(--ink);
  }
  .contact-block { position: absolute; left: 44px; top: 56px; width: 280px; }
  .contact-name { font-weight: 700; font-size: 17px; color: var(--ink); }
  .contact-title { font-size: 12px; color: var(--ink-soft); margin-top: 6px; }
  .contact-rule { height: 1px; background: var(--rule); margin: 14px 0 16px; }
  .contact-line {
    display: flex; align-items: center; gap: 12px;
    font-size: 11.5px; color: var(--ink-soft); margin-bottom: 10px;
  }
  .contact-line svg { width: 14px; height: 14px; flex: none; fill: var(--ink); }
  .contact-bottom-rule { height: 1px; background: var(--rule); margin-top: 14px; }
</style>
</head>
<body>
<main class="stage">
  <section class="card card-front" aria-label="Card front">
    <h1 class="wordmark">
      <span class="wordmark-main">VERDANT</span>
      <span class="wordmark-sub">TERRACES</span>
    </h1>
  </section>

  <section class="card card-back" aria-label="Card back">
    <div class="contact-block">
      <p class="contact-name">Colin Barrow</p>
      <p class="contact-title">Managing Director / Horticulturist</p>
      <div class="contact-rule"></div>
      <p class="contact-line">
        <svg viewBox="0 0 24 24" aria-hidden="true"><path d="M6.6 10.8a15.1 15.1 0 0 0 6.6 6.6l2.2-2.2a1 1 0 0 1 1-.25 11.4 11.4 0 0 0 3.6.57 1 1 0 0 1 1 1V20a1 1 0 0 1-1 1A17 17 0 0 1 3 4a1 1 0 0 1 1-1h3.5a1 1 0 0 1 1 1c0 1.25.2 2.45.57 3.57a1 1 0 0 1-.25 1z"/></svg>
        <span>0481 526 704</span>
      </p>
      <p class="contact-line">
        <svg viewBox="0 0 24 24" aria-hidden="true"><path d="M3 5h18a1 1 0 0 1 1 1v12a1 1 0 0 1-1 1H3a1 1 0 0 1-1-1V6a1 1 0 0 1 1-1zm9 7.2L4 7v10h16V7z"/></svg>
        <span>colinbarrow@verdantterraces.example.au</span>
      </p>
      <div class="contact-bottom-rule"></div>
    </div>
  </section>
</main>
</body>
</html>
```